Lumavento business card

We need a modern business card - With our 4 colors - See web: www.lumavento.dk

I have attached logo and som old business Cards we have - Lets Make the new ones shine...:-) -

Industry/Entity Type

Business

Requirements
Must have
• the logo with lumavento only,

```html
<!DOCTYPE html>
<html lang="da">
<head>
<meta charset="utf-8">
<title>Lumavento – visitkort</title>
<link href="https://fonts.googleapis.com/css2?family=Source+Sans+3:wght@400;600&family=Jost:wght@400&display=swap" rel="stylesheet">
<style>
  :root {
    --stage: #ecebe8;
    --paper: #ffffff;
    --lime: #a4c93a;
    --orange: #f28a1c;
    --purple: #761579;
    --magenta: #ec1a8c;
    --ink-grey: #4a4a4a;
  }
  * { margin: 0; padding: 0; box-sizing: border-box; }
  html, body { width: 1200px; height: 900px; overflow: hidden; }
  body {
    background: var(--stage);
    position: relative;
    font-family: "Source Sans 3", sans-serif;
  }
  .card { position: absolute; }
  .card-shape { position: absolute; inset: 0; }

  /* Front */
  .card-front { left: 238px; top: 62px; width: 552px; height: 343px; }
  .brand { position: absolute; left: 40px; top: 28px; width: 280px; height: 80px; }
  .brand-dot {
    position: absolute; left: 6px; top: 10px;
    width: 46px; height: 46px; border-radius: 50%;
    background: var(--lime);
  }
  .brand-name {
    position: absolute; left: 116px; top: 16px;
    font-size: 16px; letter-spacing: 2px; color: var(--ink-grey);
  }
  .brand-rule {
    position: absolute; left: 106px; top: 46px;
    width: 164px; height: 2px; background: var(--lime);
  }
  .brand-tagline {
    position: absolute; left: 130px; top: 57px;
    font-size: 12px; color: var(--ink-grey);
  }
  .person { position: absolute; left: 38px; top: 137px; }
  .person-name { font-size: 21px; font-weight: 600; color: var(--orange); line-height: 1.1; }
  .person-title { font-size: 15px; color: var(--lime); margin-top: 4px; }
  .address {
    position: absolute; left: 38px; top: 196px;
    font-size: 15px; line-height: 21px; color: var(--lime);
  }
  .contacts { position: absolute; left: 40px; top: 249px; list-style: none; }
  .contacts li {
    display: flex; align-items: center; gap: 9px;
    font-size: 15px; line-height: 23px; color: var(--lime);
  }
  .contacts svg { width: 11px; height: 11px; fill: var(--orange); }

  /* Back */
  .card-back { left: 462px; top: 518px; width: 555px; height: 342px; }
  .back-name, .back-title {
    position: absolute; left: 272px;
    font-family: "Jost", sans-serif; color: var(--paper);
    font-size: 25px; letter-spacing: 2px;
  }
  .back-name { top: 128px; }
  .back-rule {
    position: absolute; left: 265px; top: 169px;
    width: 254px; height: 5px; background: var(--paper);
  }
  .back-title { top: 180px; }
</style>
</head>
<body>

<section class="card card-front" aria-label="Visitkort, forside">
  <svg class="card-shape" viewBox="0 0 552 343" aria-hidden="true">
    <path d="M0 0 H520 Q560 40 552 170 Q545 290 470 343 H0 Z" fill="var(--paper)"/>
  </svg>
  <svg class="card-shape" viewBox="0 0 552 343" role="img" aria-label="Illustration af en limeskive">
    <path d="M395 0 H520 Q560 40 552 170 Q545 290 470 343 H300 Q330 250 358 170 Q372 80 395 0 Z" fill="var(--lime)"/>
  </svg>

  <div class="brand">
    <span class="brand-dot"></span>
    <span class="brand-name">lumavento</span>
    <span class="brand-rule"></span>
    <span class="brand-tagline">Ideer med lys</span>
  </div>

  <div class="person">
    <p class="person-name">Maren Holmgaard</p>
    <p class="person-title">Salgsdirektor</p>
  </div>

  <p class="address">Solbakkevej 12 - 4790<br>Lysbjerg -Tlf. 31 42 67 09</p>

  <ul class="contacts">
    <li><svg viewBox="0 0 12 12"><path d="M2 0.5 L4.2 0.5 L5 3.2 L3.6 4.4 Q4.8 7 7.6 8.4 L8.8 7 L11.5 7.8 L11.5 10 Q11 11.5 9.5 11.5 Q1 10.5 0.5 2.5 Q0.5 0.8 2 0.5Z"/></svg>+45 61 72 83 94</li>
    <li><svg viewBox="0 0 12 12"><path d="M0 2 H12 V10 H0 Z M0.8 2.6 L6 6.6 L11.2 2.6" stroke="#fff" stroke-width="1"/></svg>mh@lumavento.dk</li>
    <li><svg viewBox="0 0 12 12"><circle cx="6" cy="6" r="6"/></svg>www.lumavento.dk</li>
  </ul>
</section>

<section class="card card-back" aria-label="Visitkort, bagside">
  <svg class="card-shape" viewBox="0 0 555 342" aria-hidden="true">
    <path d="M90 0 H555 V342 H60 Q0 280 0 170 Q5 40 90 0 Z" fill="var(--purple)"/>
  </svg>
  <svg class="card-shape" viewBox="0 0 555 342" role="img" aria-label="Illustration af en citrusskive">
    <path d="M90 0 H150 Q185 90 190 170 Q200 260 245 342 H60 Q0 280 0 170 Q5 40 90 0 Z" fill="var(--magenta)" opacity="0.85"/>
  </svg>
  <p class="back-name">Maren Holmgaard</p>
  <span class="back-rule"></span>
  <p class="back-title">Salgsdirektør</p>
</section>

</body>
</html>
```